Automotive component supplier needs a business card design

We need a business card design for our company called Velran Global Components Ltd based in the UK. We are a supplier of interior and exterior components to premium car manufacturers such as Corvel Ashby, Hadley Fenn, Marquist and Tavarelli. We would like to see a modern business card design that uses the colour blue.

Target Market(s)

Premium automotive car manufacturers.

Industry/Entity Type

Automotive

Contact Information for Business Card

Company Name : Velran Global Components Limited
Address: 17 Marlow Yard, Upper Heath, Warwick, CV31 8QL, United Kingdom
Web Address : www.velrancomponents-example.co.uk

Font styles to use
Other font styles liked:
• Helvetica

Colors
3176b5
0255a3
85acd3
cfdeed
cee9f5
85cae6
34a6d7
0692cd
9bcb3c

Requirements
Must have
• Clear company logo and a mixture of blue colours.
Nice to have
• A high quality modern image.
Should not have
• Multiple colours.

```html
<!DOCTYPE html>
<html lang="en">
<head>
<meta charset="utf-8">
<title>Velran Global Components – Business Card</title>
<link rel="stylesheet" href="https://fonts.googleapis.com/css2?family=Open+Sans:wght@400;600;700&display=swap">
<style>
  :root {
    --blue: #0692cd;
    --blue-deep: #0a8ac6;
    --blue-pale: #cee9f5;
    --green: #9bcb3c;
    --white: #ffffff;
    --frost: #f1eeee;
    --frost-back: #ece6e3;
    --stage: #e9e7e6;
    --ink-light: #ffffff;
  }
  * { box-sizing: border-box; margin: 0; padding: 0; }
  html, body { width: 1200px; height: 900px; overflow: hidden; }
  body {
    background: var(--stage);
    font-family: "Open Sans", Helvetica, Arial, sans-serif;
    position: relative;
  }
  .card {
    position: absolute;
    width: 558px;
    height: 344px;
    display: flex;
    box-shadow: 0 4px 14px rgba(0,0,0,0.08);
  }
  .card--front { left: 236px; top: 61px; }
  .card--back  { left: 459px; top: 518px; width: 560px; }

  /* front */
  .front__brand {
    width: 268px;
    background: var(--frost);
    display: flex;
    align-items: center;
    justify-content: center;
    gap: 10px;
  }
  .brand-mark {
    width: 22px; height: 22px;
    background: var(--green);
    border-radius: 4px;
    flex: none;
  }
  .brand-name {
    color: var(--blue);
    font-weight: 700;
    font-size: 25px;
    line-height: 1.05;
    letter-spacing: 0.5px;
  }
  .front__details {
    flex: 1;
    background: var(--blue);
    color: var(--ink-light);
    padding: 50px 24px 0 23px;
  }
  .person__name { font-weight: 600; font-size: 19px; line-height: 1.2; }
  .person__role { font-size: 14px; line-height: 1.3; }
  .address { margin-top: 18px; font-size: 14px; line-height: 20px; font-style: normal; }
  .contacts { list-style: none; margin-top: 21px; font-size: 14px; line-height: 20px; }
  .contacts li { display: flex; align-items: center; gap: 9px; white-space: nowrap; }
  .contacts svg { width: 11px; height: 11px; fill: var(--ink-light); flex: none; }
  .contacts .small { font-size: 12.5px; }

  /* back */
  .back__brand {
    width: 303px;
    background: var(--white);
    display: flex;
    flex-direction: column;
    justify-content: center;
    padding-left: 28px;
    color: var(--blue-deep);
    font-weight: 700;
  }
  .back__name { font-size: 40px; line-height: 1; letter-spacing: 1px; }
  .back__tagline { font-size: 12.5px; letter-spacing: 1.4px; margin-top: 6px; }
  .back__panel {
    flex: 1;
    background: var(--frost-back);
    position: relative;
  }
  .back__shape {
    position: absolute;
    left: 36px; top: 102px;
    width: 40px; height: 40px;
    background: var(--blue-pale);
    border-radius: 6px;
  }
</style>
</head>
<body>
  <section class="card card--front" aria-label="Business card front">
    <div class="front__brand">
      <span class="brand-mark"></span>
      <span class="brand-name">Velran<br>Global<br>Components</span>
    </div>
    <div class="front__details">
      <p class="person__name">Ellis Marr</p>
      <p class="person__role">Director</p>
      <address class="address">
        17 Marlow Yard,<br>Upper Heath,<br>Warwick, CV31 8QL,<br>United Kingdom
      </address>
      <ul class="contacts">
        <li><svg viewBox="0 0 24 24"><path d="M6.6 10.8a15.1 15.1 0 0 0 6.6 6.6l2.2-2.2a1 1 0 0 1 1-.25 11.4 11.4 0 0 0 3.6.57 1 1 0 0 1 1 1V20a1 1 0 0 1-1 1A17 17 0 0 1 3 4a1 1 0 0 1 1-1h3.5a1 1 0 0 1 1 1c0 1.25.2 2.45.57 3.57a1 1 0 0 1-.25 1z"/></svg>01926 555 014</li>
        <li><svg viewBox="0 0 24 24"><path d="M7 1h10a2 2 0 0 1 2 2v18a2 2 0 0 1-2 2H7a2 2 0 0 1-2-2V3a2 2 0 0 1 2-2zm0 3v14h10V4zm5 15.5a1.2 1.2 0 1 0 0 2.4 1.2 1.2 0 0 0 0-2.4z"/></svg>07700 900 482</li>
        <li class="small"><svg viewBox="0 0 24 24"><path d="M2 5h20v14H2zm2 2v.5l8 5 8-5V7zm0 2.8V17h16V9.8l-8 5z"/></svg>info@velrancomponents-example.co.uk</li>
        <li class="small"><svg viewBox="0 0 24 24"><path d="M12 2a10 10 0 1 0 0 20 10 10 0 0 0 0-20zm-1 17.9A8 8 0 0 1 4.2 10.6L9 15.4v1a2 2 0 0 0 2 2zm6.9-2.5A2 2 0 0 0 16 16h-1v-3a1 1 0 0 0-1-1H8v-2h2a1 1 0 0 0 1-1V7h2a2 2 0 0 0 2-2v-.4a8 8 0 0 1 2.9 12.8z"/></svg>www.velrancomponents-example.co.uk</li>
      </ul>
    </div>
  </section>

  <section class="card card--back" aria-label="Business card back">
    <div class="back__brand">
      <span class="back__name">VELRAN</span>
      <span class="back__tagline">GLOBAL COMPONENTS</span>
    </div>
    <div class="back__panel">
      <span class="back__shape"></span>
    </div>
  </section>
</body>
</html>
```